Ashwell Court Apartments
stationary
Project: Ashwell Court Apartments
Ashwell Court Apartments - Real Estate
Creative Brief
Traditional
Daniel Kessing
2430 Ashwell Court Houston TX 77091
dpkessing@mailvora.net

```html
<!DOCTYPE html>
<html lang="en">
<head>
<meta charset="utf-8">
<title>Ashwell Court Apartments — Business Card</title>
<link rel="stylesheet" href="https://fonts.googleapis.com/css2?family=Cinzel:wght@500&family=EB+Garamond:wght@400&display=swap">
<style>
  :root {
    --page: #e9eaec;
    --green: #2f8c3c;
    --green-dark: #25742f;
    --white: #ffffff;
    --ink: #1c1c1c;
  }
  html, body {
    margin: 0;
    padding: 0;
    width: 1200px;
    height: 1009px;
    overflow: hidden;
    background: var(--page);
  }
  .sheet {
    position: relative;
    width: 1200px;
    height: 1009px;
  }
  .card {
    position: absolute;
    left: 250px;
    width: 700px;
    height: 400px;
    border-radius: 22px;
    overflow: hidden;
    background: var(--green);
    box-shadow: 0 6px 18px rgba(0,0,0,0.18);
  }
  .card--back { top: 70px; }
  .card--front { top: 540px; }

  .wordmark {
    font-family: "Cinzel", serif;
    font-weight: 500;
    text-align: center;
    letter-spacing: 2px;
    line-height: 1.15;
  }
  .wordmark__dot {
    display: block;
    margin: 0 auto 14px;
    border-radius: 50%;
  }

  .card--back .wordmark {
    position: absolute;
    left: 0; right: 0;
    top: 118px;
    color: var(--white);
    font-size: 40px;
  }
  .card--back .wordmark__dot {
    width: 46px; height: 46px;
    background: var(--white);
  }

  .front-art {
    position: absolute;
    inset: 0;
  }
  .card--front .wordmark {
    position: absolute;
    left: 30px;
    top: 92px;
    width: 300px;
    color: var(--green);
    font-size: 27px;
  }
  .card--front .wordmark__dot {
    width: 36px; height: 36px;
    background: var(--green);
  }

  .holder-name {
    position: absolute;
    right: 48px;
    top: 62px;
    margin: 0;
    font-family: "Cinzel", serif;
    font-weight: 500;
    font-size: 21px;
    letter-spacing: 1.5px;
    color: var(--white);
  }
  .contact {
    position: absolute;
    right: 48px;
    bottom: 50px;
    margin: 0;
    padding: 0;
    list-style: none;
    font-family: "EB Garamond", serif;
    font-size: 20px;
    line-height: 1.45;
    color: var(--white);
    text-align: right;
  }
  .contact__row {
    display: flex;
    justify-content: flex-end;
    align-items: center;
    gap: 12px;
  }
  .contact__icon {
    width: 16px;
    height: 16px;
    flex: none;
  }
  .contact__spacer { width: 16px; flex: none; }
</style>
</head>
<body>
<main class="sheet">

  <section class="card card--back" aria-label="Card back">
    <div class="wordmark">
      <span class="wordmark__dot"></span>
      Ashwell Court<br>Apartments
    </div>
  </section>

  <section class="card card--front" aria-label="Card front">
    <svg class="front-art" width="700" height="400" viewBox="0 0 700 400" aria-hidden="true">
      <path d="M0 0 H300 C430 50 440 300 300 400 H0 Z" fill="var(--ink)"/>
      <path d="M0 0 H280 C410 45 410 300 260 392 C200 400 120 400 0 400 Z" fill="var(--white)"/>
    </svg>

    <div class="wordmark">
      <span class="wordmark__dot"></span>
      Ashwell Court<br>Apartments
    </div>

    <h1 class="holder-name">Daniel Kessing</h1>

    <ul class="contact">
      <li class="contact__row">
        <span>2430 Ashwell Court</span>
        <svg class="contact__icon" viewBox="0 0 16 16" aria-hidden="true">
          <path d="M8 1a5 5 0 0 0-5 5c0 4 5 9 5 9s5-5 5-9a5 5 0 0 0-5-5zm0 7a2 2 0 1 1 0-4 2 2 0 0 1 0 4z" fill="var(--white)"/>
        </svg>
      </li>
      <li class="contact__row"><span>Houston TX 77091</span><span class="contact__spacer"></span></li>
      <li class="contact__row">
        <span>713-555-0148</span>
        <svg class="contact__icon" viewBox="0 0 16 16" aria-hidden="true">
          <path d="M4 1.5l2.2 3-1.4 1.4c.8 1.8 2.1 3.1 3.9 3.9l1.4-1.4 3 2.2-1.2 2.6C7 13 3 9 1.4 2.7z" fill="var(--white)"/>
        </svg>
      </li>
      <li class="contact__row">
        <span>dpkessing@mailvora.net</span>
        <svg class="contact__icon" viewBox="0 0 16 16" aria-hidden="true">
          <rect x="1.5" y="3.5" width="13" height="9" fill="none" stroke="var(--white)" stroke-width="1.4"/>
          <path d="M1.5 3.5 L8 9 L14.5 3.5" fill="none" stroke="var(--white)" stroke-width="1.4"/>
        </svg>
      </li>
    </ul>
  </section>

</main>
</body>
</html>
```